Business card design

Hi,
I need to have a business card design based on the current logo.
If competitive I not put it out to everyone.

It can be single of double sided

Target Market(s)

Food businesses

Industry/Entity Type

Food Manufacturing

Contact Information for Business Card

Details will on card will be as follows Name = Marcus Bell Email = Marcus@PanHearth.com.au Phone = 0418563207 Address = 57 Larkin Street , Fortitude Valley QLD 4006 Australia

Font styles to use
Other font styles liked:
• based on two fonts - Adelle & Museo

Requirements
Must have
• Based on the on switch concept

```html
<!DOCTYPE html>
<html lang="en">
<head>
<meta charset="utf-8">
<title>PanHearth — Business Card</title>
<link rel="stylesheet" href="https://fonts.googleapis.com/css2?family=Arimo:wght@400;700&display=swap">
<style>
  :root {
    --card-red: #ee2a47;
    --ink-white: #ffffff;
    --brand-dark: #3a2a2e;
    --page-bg: #ecebea;
    --frost-light: #f4f1f1;
    --frost-mid: #d9d4d4;
    --frost-deep: #bdb5b6;
  }
  * { box-sizing: border-box; margin: 0; padding: 0; }
  html, body {
    width: 1200px;
    height: 900px;
    overflow: hidden;
    background: var(--page-bg);
    font-family: "Arimo", Arial, sans-serif;
  }
  .canvas {
    position: relative;
    width: 1200px;
    height: 900px;
  }
  .card-shape {
    position: absolute;
    left: 0;
    top: 0;
  }
  .card-name {
    position: absolute;
    left: 168px;
    top: 220px;
    font-size: 42px;
    font-weight: 700;
    letter-spacing: 0.5px;
    color: var(--ink-white);
    text-transform: uppercase;
  }
  .card-address {
    position: absolute;
    left: 168px;
    top: 391px;
    font-style: normal;
    font-size: 28px;
    line-height: 36px;
    color: var(--ink-white);
  }
  .card-contacts {
    position: absolute;
    left: 168px;
    top: 594px;
    list-style: none;
    color: var(--ink-white);
    font-size: 28px;
    line-height: 36px;
  }
  .contact-row {
    display: flex;
    align-items: center;
    gap: 10px;
  }
  .contact-icon {
    width: 26px;
    height: 26px;
    flex: none;
  }
</style>
</head>
<body>
<main class="canvas">
  <svg class="card-shape" width="1200" height="900" viewBox="0 0 1200 900" aria-hidden="true">
    <defs>
      <radialGradient id="frost" cx="45%" cy="40%" r="70%">
        <stop offset="0%" stop-color="var(--frost-light)"/>
        <stop offset="60%" stop-color="var(--frost-mid)"/>
        <stop offset="100%" stop-color="var(--frost-deep)"/>
      </radialGradient>
    </defs>
    <path class="card-body" d="M110 146 H789.5 A302.5 302.5 0 0 1 789.5 751 H110 Z" fill="var(--card-red)"/>
    <circle class="frosted-window" cx="783" cy="452" r="261" fill="url(#frost)"/>
    <g class="brand-lockup">
      <circle cx="627" cy="452" r="20" fill="var(--card-red)"/>
      <text x="659" y="469" font-family="Arimo, Arial, sans-serif" font-size="46" font-weight="700" fill="var(--brand-dark)">PANHEARTH</text>
    </g>
  </svg>

  <h1 class="card-name">Marcus Bell</h1>

  <address class="card-address">
    57 Larkin Street<br>
    Ashcombe Vale<br>
    QLD 4185 Australia
  </address>

  <ul class="card-contacts">
    <li class="contact-row">
      <svg class="contact-icon" viewBox="0 0 24 24" aria-hidden="true">
        <path d="M6.6 2.5 9.4 6 7.8 8.3c1 2.7 3.2 5 5.9 6l2.3-1.6 3.5 2.8-1.6 3.2c-.5.8-1.5 1.2-2.4.9C9.4 17.7 6.3 14.6 4.4 8.5c-.3-.9.1-1.9.9-2.4Z" fill="var(--ink-white)"/>
        <path d="M14 3.5a7 7 0 0 1 6.5 6.5M14 7a3.5 3.5 0 0 1 3 3" stroke="var(--ink-white)" stroke-width="1.8" fill="none" stroke-linecap="round"/>
      </svg>
      <span>0418563207</span>
    </li>
    <li class="contact-row">
      <svg class="contact-icon" viewBox="0 0 24 24" aria-hidden="true">
        <rect x="1" y="5" width="22" height="14" fill="var(--ink-white)"/>
        <path d="M1 5 12 13 23 5" stroke="var(--card-red)" stroke-width="1.6" fill="none"/>
      </svg>
      <span>Marcus@PanHearth.com.au</span>
    </li>
    <li class="contact-row">
      <svg class="contact-icon" viewBox="0 0 24 24" aria-hidden="true">
        <g stroke="var(--ink-white)" stroke-width="1.7" fill="none">
          <circle cx="12" cy="12" r="10"/>
          <ellipse cx="12" cy="12" rx="4.5" ry="10"/>
          <path d="M2 12h20M4 6.5h16M4 17.5h16"/>
        </g>
      </svg>
      <span>www.PanHearth.com.au</span>
    </li>
  </ul>
</main>
</body>
</html>
```